KAJU Freightways #ALLKAJU Business Cards & Letterhead

I am looking to business cards designed for our organization. We are currently undergoing a small re-branding that is taking place. Our organization is called KAJU Freightways and we are headquartered in Phoenix, AZ. We primarily provide transportation and logistics services to the Marlow Parcel Bureau who is our largest customer. I would like to see a design that incorporates name, title, contact info, website, and address (this will be different depending on the employee). I would also like to see some color on the business card using our logo colors or a variation. I would like our logo on the back of the business card with the website displayed. The final design should communicate that we are a next generation transportation operate that focuses on being driver-first, customer-centric, innovative, and sustainable.We would also like our #ALLKAJU catch phrase incorporated as well.

Target Market(s)

Transportation & Logistics

Industry/Entity Type

Trucking Company

Contact Information for Business Card

-First and Last Name
-Position Title
-Contact Phone
-Contact Email
-Physical Address

Font styles to use
Serif

Colors

Designer to choose colors to be used in the design.

Requirements
Must have
• -KAJU logo prominently displayed
• -#ALLKAJU catch phrase used
• -Some amount of color, design gradient, etc.
• -Logo on the back with website listed (https://www.kajufreightco.example)

```html
<!DOCTYPE html>
<html lang="en">
<head>
<meta charset="utf-8">
<title>KAJU Freightways Business Card</title>
<link href="https://fonts.googleapis.com/css2?family=Roboto+Slab:wght@400;500;700&display=swap" rel="stylesheet">
<style>
  :root {
    --backdrop: #3b3b3d;
    --card: #1d1d1f;
    --card-edge: #262628;
    --lime: #7cc520;
    --teal: #0b4651;
    --stripe: #3a3a3c;
    --white: #ffffff;
    --emboss: #5a5a5d;
    --muted: #d9d9d9;
  }
  * { margin: 0; padding: 0; box-sizing: border-box; }
  html, body { width: 799px; height: 1200px; overflow: hidden; }
  body {
    background: var(--backdrop);
    font-family: "Roboto Slab", Georgia, serif;
    position: relative;
  }
  .card {
    position: absolute;
    left: 70px;
    width: 660px;
    height: 377px;
    background: var(--card);
    border: 1px solid var(--card-edge);
    box-shadow: 0 14px 30px rgba(0,0,0,.45);
    overflow: hidden;
  }
  .card--back { top: 110px; }
  .card--front { top: 700px; }
  .card > svg { position: absolute; inset: 0; }

  /* back face */
  .back-site {
    position: absolute;
    left: 0; right: 0; top: 300px;
    text-align: center;
    color: var(--muted);
    font-size: 16px;
    letter-spacing: 4px;
  }
  .back-site::before, .back-site::after {
    content: "";
    display: inline-block;
    width: 34px; height: 3px;
    background: var(--lime);
    vertical-align: middle;
    margin: 0 26px;
  }

  /* front face */
  .person {
    position: absolute;
    right: 34px; top: 48px;
    text-align: right;
    color: var(--white);
  }
  .person-name { font-size: 26px; font-weight: 700; line-height: 1.2; }
  .person-title { font-size: 16px; color: var(--lime); margin-top: 2px; }
  .person-address { font-size: 14px; line-height: 1.35; margin-top: 8px; }
  .contact {
    position: absolute;
    right: 34px; top: 246px;
    text-align: right;
    color: var(--white);
  }
  .contact-tagline { font-size: 16px; font-weight: 700; line-height: 1.1; margin-bottom: 5px; }
  .contact-row { font-size: 14px; line-height: 1.45; display: flex; justify-content: flex-end; align-items: center; gap: 9px; }
  .contact-row svg { width: 14px; height: 14px; flex: none; }
  .hashtag {
    position: absolute;
    left: 30px; bottom: 22px;
    color: var(--lime);
    font-size: 18px;
    font-weight: 700;
    letter-spacing: 1px;
  }
</style>
</head>
<body>

<section class="card card--back" aria-label="Card back">
  <svg viewBox="0 0 660 377" width="660" height="377">
    <circle cx="330" cy="150" r="100" fill="none" stroke="var(--emboss)" stroke-width="6"/>
    <text x="330" y="171" text-anchor="middle" font-family="Roboto Slab, Georgia, serif" font-weight="700" font-size="60" fill="var(--emboss)">KAJU</text>
  </svg>
  <p class="back-site">www.kajufreightco.example</p>
</section>

<section class="card card--front" aria-label="Card front">
  <svg viewBox="0 0 660 377" width="660" height="377">
    <path d="M0,232 C90,247 160,292 250,294 C380,297 520,232 660,217 L660,377 L0,377 Z" fill="var(--teal)"/>
    <path d="M0,218 C90,233 160,278 250,280 C380,283 520,218 660,203 L660,217 C520,232 380,297 250,294 C160,292 90,247 0,232 Z" fill="var(--stripe)"/>
    <path d="M0,202 C90,217 160,262 250,264 C380,267 520,202 660,187 L660,203 C520,218 380,283 250,280 C160,278 90,233 0,218 Z" fill="var(--lime)"/>
    <path d="M80,180 C130,225 190,250 270,256" fill="none" stroke="var(--lime)" stroke-width="2.5"/>
    <circle cx="150" cy="102" r="86" fill="none" stroke="var(--lime)" stroke-width="6"/>
    <text x="150" y="121" text-anchor="middle" font-family="Roboto Slab, Georgia, serif" font-weight="700" font-size="52" fill="var(--white)">KAJU</text>
  </svg>

  <div class="person">
    <h1 class="person-name">Dana Whitcombe</h1>
    <p class="person-title">Chairman &amp; CEO</p>
    <p class="person-address">4410 West Cactus Ridge Road<br>Glendale, AZ 85308</p>
  </div>

  <div class="contact">
    <p class="contact-tagline">Transportation &amp;<br>Energy Services</p>
    <p class="contact-row">623-555-0148
      <svg viewBox="0 0 16 16" aria-hidden="true"><path d="M3 2h3l1 4-2 1a9 9 0 0 0 4 4l1-2 4 1v3c0 1-1 1-1 1C7 14 2 9 2 3c0 0 0-1 1-1z" fill="var(--lime)"/></svg>
    </p>
    <p class="contact-row">www.kajufreightco.example
      <svg viewBox="0 0 16 16" aria-hidden="true"><circle cx="8" cy="8" r="6.5" fill="none" stroke="var(--lime)" stroke-width="1.5"/><path d="M1.5 8h13M8 1.5c-3 3.5-3 9.5 0 13M8 1.5c3 3.5 3 9.5 0 13" fill="none" stroke="var(--lime)" stroke-width="1.2"/></svg>
    </p>
    <p class="contact-row">dana@kajufreightco.example
      <svg viewBox="0 0 16 16" aria-hidden="true"><rect x="1" y="3" width="14" height="10" fill="var(--lime)"/><path d="M1 3l7 6 7-6" fill="none" stroke="var(--teal)" stroke-width="1.4"/></svg>
    </p>
  </div>

  <p class="hashtag">#ALLKAJU</p>
</section>

</body>
</html>
```